Floravine Pte Ltd

I want a creative and stand out web page so when my client search for my web page or google search. The front page is stand out and they know that we are the interior office designer that are searching for . We are commercial office design company. We also have the video to put at our front page for client to see. Natural is the key elements. As we like to carry recycle materials , plant , trees is our key element such as biophilic design
Updates

Hi All,

For my web page, I need minimalist design and creative frontpage.
When my client search for my web page, they straight feel that this is the office design company.
The webpage is special and nature is the key element for the design.
My company logo can be design in the shaped of the letter OO in the webpage.
Below is the sample you can refer.

https://www.pinboardly.example/pin/527190364821057392/

Target Market(s)

Customer searching for office design

Industry/Entity Type

Commerical designer firm- Office interior design & Build company

Number of Pages Required

5+ page

Font styles to use
Other font styles liked:
• Wilmina

Colors
59FF00
82FF00
B8FF75
E3FFCB
F4FFEA
FFC000
F8CF3A
FAE287
FDF2CF
FEFAEE
6B429C
8869AF
B7A5CE
E3DAEB
F3F0F8

Requirements
Must have
• Home, Services,Gallery, Calculator, Testimonials, Contact, Blog
Nice to have
• Natural, creative, minimalist
Should not have
• No black color or blue color

```html
<!DOCTYPE html>
<html lang="en">
<head>
<meta charset="utf-8">
<title>Floravine Pte Ltd – Office Design &amp; Renovation</title>
<link rel="stylesheet" href="https://fonts.googleapis.com/css2?family=Nunito+Sans:wght@300;400;600;700;800&display=swap">
<style>
:root{
  --ink:#2b2b2b;
  --ink-soft:#4a4a4a;
  --muted:#8a8a8a;
  --rule:#9a9a9a;
  --accent:#ffc000;
  --accent-soft:#f8cf3a;
  --brand:#e8502a;
  --band:#f4f2f2;
  --white:#ffffff;
}
*{margin:0;padding:0;box-sizing:border-box}
html,body{width:1200px;height:5102px;overflow:hidden}
body{position:relative;background:var(--white);font-family:"Nunito Sans",Arial,sans-serif;color:var(--ink)}
.abs{position:absolute}
.photo{position:absolute}

/* hero */
.hero{left:0;top:0;width:1200px;height:574px;background:radial-gradient(ellipse at 50% 30%,#c9a27a 0%,#8b6446 45%,#4b3324 100%)}
.brand-mark{display:flex;align-items:center;gap:8px;font-weight:600;color:var(--brand);font-size:21px}
.brand-dot{width:26px;height:26px;border-radius:50%;border:4px solid var(--brand)}
.nav{left:374px;top:28px;display:flex;gap:0;font-size:12.5px;color:var(--white);letter-spacing:.3px}
.nav a{color:inherit;text-decoration:none;margin-right:31px;padding-bottom:6px}
.nav a.current{border-bottom:2px solid var(--white)}
.play{left:556px;top:223px;width:48px;height:48px;border-radius:50%;background:var(--white)}
.hero-title{left:150px;top:336px;width:900px;text-align:center;color:var(--white);font-weight:800;font-size:25px;line-height:37px;text-transform:uppercase;text-shadow:0 2px 4px rgba(60,40,20,.7)}
.hero-knob{left:553px;top:517px;width:42px;height:36px;border-radius:50%;background:#4a3a30}

/* headings */
.sec-title{width:1200px;left:0;text-align:center;font-size:29px;line-height:36px}
.sec-title b{font-weight:800}
.sec-title span{font-weight:400}
.gold-line{height:4px;width:68px;background:var(--accent)}

/* services */
.service{top:782px;width:281px}
.service .photo{position:relative;width:281px;height:288px}
.service h3{font-weight:400;font-size:17px;margin-top:23px;text-align:center}
.more{position:absolute;right:6px;top:352px;display:flex;align-items:center;gap:10px;font-size:10px;color:var(--accent);letter-spacing:.5px}
.more i{display:block;width:68px;height:1px;background:var(--accent)}

/* welcome */
.welcome-title{left:130px;top:1246px;font-size:30px;line-height:44px}
.welcome-title b{font-weight:800}
.welcome-intro{left:634px;top:1250px;width:420px;font-size:21px;line-height:32px;font-weight:400}
.body-copy{font-size:13.4px;line-height:22.6px;color:var(--ink-soft);text-align:justify}
.btn{background:var(--accent);color:var(--white);font-weight:700;font-size:13px;display:flex;align-items:center;justify-content:center}

/* calculators */
.calc{top:2100px;width:320px;text-align:center}
.calc h4{font-weight:400;font-size:17px;line-height:23px;margin-top:16px;text-transform:uppercase}
.calc p{font-size:13px;line-height:22px;color:var(--ink-soft);margin-top:18px;padding:0 20px}

/* gallery */
.tile{width:386px;height:380px}
.tile .tag{position:absolute;left:0;top:0;background:var(--white);font-size:12.5px;padding:5px 8px;text-transform:uppercase}

/* customers */
.client{top:4320px;width:168px;height:86px;border:2px solid var(--ink);display:flex;align-items:center;justify-content:center;font-weight:800;font-size:22px;color:var(--ink)}
.arrow{top:4345px;font-size:32px;color:var(--ink);font-weight:300}

/* footer */
.foot-head{font-weight:700;font-size:12px;letter-spacing:.3px}
.foot-list{font-size:11.5px;line-height:19.5px;color:var(--ink-soft);text-transform:uppercase;margin-top:12px}
</style>
</head>
<body>

<!-- HERO -->
<header>
  <div class="abs hero" role="img" aria-label="Video still of a warm timber-lined office reception with a long white front desk"></div>
  <div class="abs brand-mark" style="left:32px;top:22px"><span class="brand-dot"></span>Floravine pte ltd</div>
  <nav class="abs nav">
    <a class="current" href="#">HOME</a><a href="#">SERVICES</a><a href="#">GALLERY</a><a href="#">PORTFOLIO</a><a href="#">CALCULATOR</a><a href="#">TESTIMONIALS</a><a href="#">CONTACT</a><a href="#">BLOG</a>
  </nav>
  <div class="abs play">
    <svg width="48" height="48" viewBox="0 0 48 48"><path d="M19 14 L34 24 L19 34 Z" fill="#4b3324"/></svg>
  </div>
  <h1 class="abs hero-title">Bring goods straight from factory and cut away the middleman costing so client can have a better quality with affordable price.</h1>
  <div class="abs hero-knob"></div>
</header>

<!-- ONE-STOP -->
<section>
  <h2 class="abs sec-title" style="top:622px"><b>YOUR ONE-STOP OFFICE RENOVATION</b><br><span>&amp; INTERIOR DESIGN PARTNER</span></h2>
  <div class="abs gold-line" style="left:566px;top:731px"></div>

  <article class="abs service" style="left:14px">
    <div class="photo" role="img" aria-label="Office lounge with a living green wall" style="background:linear-gradient(160deg,#3d5a2c,#2a3a22 60%,#7a6a58)"></div>
    <h3>OFFICE INTERIOR DESIGN</h3>
    <div class="more"><i></i>MORE</div>
  </article>
  <article class="abs service" style="left:311px">
    <div class="photo" role="img" aria-label="Bright open-plan office with rows of workstations" style="background:linear-gradient(180deg,#f2f2f0,#d9d9d6 60%,#7d7f82)"></div>
    <h3>OFFICE RENOVATION</h3>
    <div class="more"><i></i>MORE</div>
  </article>
  <article class="abs service" style="left:608px">
    <div class="photo" role="img" aria-label="Team gathered around a table planning an office layout" style="background:linear-gradient(160deg,#c7d3dc,#8a97a3 50%,#6d5f52)"></div>
    <h3>OFFICE SPACE PLANNING</h3>
    <div class="more"><i></i>MORE</div>
  </article>
  <article class="abs service" style="left:905px">
    <div class="photo" role="img" aria-label="Office divided by a timber partition wall" style="background:linear-gradient(90deg,#e7e5e3,#cfc9c4 55%,#6e3e2a 60%,#d8d4d0 72%)"></div>
    <h3>OFFICE SPACE PARTITIONING</h3>
    <div class="more"><i></i>MORE</div>
  </article>
</section>

<!-- WELCOME -->
<section>
  <div class="abs" style="left:548px;top:1208px;width:1px;height:138px;background:var(--rule)"></div>
  <h2 class="abs welcome-title"><b>WELCOME TO</b><br>FLORAVINE SINGAPORE</h2>
  <div class="abs gold-line" style="left:130px;top:1344px"></div>
  <p class="abs welcome-intro">A Singapore Reputable Commercial Interior Design &amp; Office Renovation Company</p>
  <div class="photo" role="img" aria-label="Open office with desks facing a floor-to-ceiling plant wall" style="left:28px;top:1404px;width:665px;height:430px;background:linear-gradient(150deg,#56703a,#3c5a2a 45%,#b89a72 80%,#8e7354)"></div>
  <p class="abs body-copy" style="left:735px;top:1468px;width:305px">No matter what type of commercial space you have, whether it is an office, corporate firm, restaurant, spa, salon, plaza, mall, or any retail shop, we are here to provide the highest level of interior design and renovation services to match your needs. Our creative ideas and innovative solutions to commercial renovation projects can transform any workspace or building into a masterpiece.</p>
  <div class="abs btn" style="left:737px;top:1707px;width:221px;height:34px">Read more about FLORAVINE.</div>
</section>

<!-- CALCULATORS -->
<section>
  <div class="abs" style="left:438px;top:1917px;width:1px;height:453px;background:var(--rule)"></div>
  <div class="abs" style="left:780px;top:1917px;width:1px;height:453px;background:var(--rule)"></div>
  <div class="abs" style="left:133px;top:2043px;width:934px;height:1px;background:var(--rule)"></div>
  <h2 class="abs" style="left:438px;width:342px;top:1926px;text-align:center;font-size:30px;line-height:44px"><b style="font-weight:800">OUR</b><br>CALCULATORS</h2>

  <article class="abs calc" style="left:117px">
    <svg width="76" height="76" viewBox="0 0 76 76" fill="none" stroke="#ffc000" stroke-width="2.5">
      <rect x="20" y="14" width="36" height="54"/><path d="M28 8h20v6M12 68h52"/>
      <path d="M26 22h6M36 22h6M46 22h4M26 32h6M36 32h6M46 32h4M26 42h6M36 42h6M46 42h4"/><rect x="32" y="54" width="12" height="14"/>
    </svg>
    <h4>Office Floor<br>Space Calculator</h4>
    <p>Unsure how much office space do you need for renovation? Use our office space calculator here.</p>
  </article>
  <article class="abs calc" style="left:438px;width:320px">
    <svg width="76" height="76" viewBox="0 0 76 76" fill="none" stroke="#ffc000" stroke-width="2.5">
      <path d="M18 8h26l10 10v22"/><path d="M18 8v52h14"/><circle cx="26" cy="30" r="6"/>
      <rect x="36" y="38" width="28" height="32" rx="2"/><rect x="40" y="42" width="20" height="7"/>
      <path d="M42 55h3M49 55h3M56 55h3M42 62h3M49 62h3M56 62h3"/>
    </svg>
    <h4>Renovation<br>Budget Calculator</h4>
    <p>How much should you budget for office renovation? Try out our renovation budget calculator here.</p>
  </article>
  <article class="abs calc" style="left:775px">
    <svg width="76" height="76" viewBox="0 0 76 76" fill="none" stroke="#ffc000" stroke-width="2.5">
      <rect x="36" y="10" width="30" height="10" rx="2"/><rect x="36" y="26" width="30" height="10" rx="2"/><rect x="36" y="42" width="30" height="10" rx="2"/><rect x="36" y="58" width="30" height="10" rx="2"/>
      <circle cx="18" cy="38" r="9"/><path d="M18 33v5h4M27 38h9M30 15v8M30 31v7M30 47v16"/>
    </svg>
    <h4>Project Timeline<br>Calculator</h4>
    <p>In order to know your office renovation and relocation timescale. Use this project timeline calculator.</p>
  </article>
</section>

<!-- GALLERY -->
<section>
  <h2 class="abs sec-title" style="top:2481px"><b>PROJECT</b> <span>GALLERY</span></h2>
  <p class="abs" style="left:0;width:1200px;top:2535px;text-align:center;font-size:19px;color:var(--ink-soft)">Explore our work. Let our design portfolio speaks for itself.</p>

  <figure class="photo tile" style="left:8px;top:2637px" role="img" aria-label="Cafeteria with round tables and large city-view windows"><div style="position:absolute;inset:0;background:linear-gradient(170deg,#d8cdb8,#9aa2a6 45%,#5b5450)"></div><figcaption class="tag">Harbourline Singapore</figcaption></figure>
  <figure class="photo tile" style="left:406px;top:2637px" role="img" aria-label="Reception with frosted glass doors and yellow floral wallpaper"><div style="position:absolute;inset:0;background:linear-gradient(90deg,#c9b23a,#b8b4a8 35%,#9fa3a8 65%,#c8b13c)"></div><figcaption class="tag">STRM Group</figcaption></figure>
  <figure class="photo tile" style="left:804px;top:2637px" role="img" aria-label="Boardroom with glowing ceiling coffers and wood panelling"><div style="position:absolute;inset:0;background:linear-gradient(180deg,#e7c27a,#8a5a2c 40%,#5a3a1c 70%,#c8822a)"></div><figcaption class="tag">Suryapadi Holdings</figcaption></figure>
  <figure class="photo tile" style="left:8px;top:3033px" role="img" aria-label="Meeting room with long white table and grey blinds"><div style="position:absolute;inset:0;background:linear-gradient(170deg,#d9d6d3,#aaa6a2 50%,#5a5552)"></div><figcaption class="tag">Meridale Hotels</figcaption></figure>
  <figure class="photo tile" style="left:406px;top:3033px" role="img" aria-label="Timber staircase against a pale concrete wall"><div style="position:absolute;inset:0;background:linear-gradient(160deg,#e4e2de,#c9c5bf 50%,#b98a4c 75%,#8d6a3c)"></div><figcaption class="tag">Harbourline Kuala Lumpur</figcaption></figure>
  <figure class="photo tile" style="left:804px;top:3033px" role="img" aria-label="Meeting room with white table, tall chairs and purple carpet"><div style="position:absolute;inset:0;background:linear-gradient(180deg,#8a8074,#d9e4e4 40%,#f1f1f1 65%,#6e4f9a)"></div><figcaption class="tag">Veritra Singapore</figcaption></figure>

  <div class="abs btn" style="left:525px;top:3445px;width:148px;height:34px">View All Images</div>
</section>

<!-- GREEN DESIGN -->
<section>
  <div class="photo" role="img" aria-label="Industrial-style office with green plant walls, exposed ducts and timber desks" style="left:327px;top:3534px;width:873px;height:618px;background:linear-gradient(120deg,#3a3430,#4f6a30 35%,#6d8a3e 55%,#7a5a3e 75%,#3c3530)"></div>
  <div class="abs" style="left:0;top:3600px;width:548px;height:479px;background:var(--white)"></div>
  <h2 class="abs" style="left:158px;top:3664px;font-size:30px;line-height:44px"><b style="font-weight:800">THE GREEN DESIGN</b><br>REVOLUTION</h2>
  <p class="abs body-copy" style="left:158px;top:3796px;width:335px">With our commitment to support eco-friendly solutions, we specialise in ‘green design’. Our interior design solutions contribute positively to the overall health of the inhabitants of a specific area while considering various environmental factors. We ensure that a sustainable solution will be catered to you. Our green design is balance with aesthetics, functionality, and design quality.</p>
  <div class="abs btn" style="left:158px;top:4000px;width:109px;height:33px">Read More</div>
</section>

<!-- CUSTOMERS -->
<section>
  <h2 class="abs sec-title" style="top:4205px"><b>OUR</b> <span>CUSTOMERS</span></h2>
  <div class="abs arrow" style="left:20px">‹</div>
  <div class="abs client" style="left:59px">Arcomba</div>
  <div class="abs client" style="left:246px">Nuvex</div>
  <div class="abs client" style="left:428px">Suitelane</div>
  <div class="abs client" style="left:610px">Woodcrest</div>
  <div class="abs client" style="left:794px">Baroletti</div>
  <div class="abs client" style="left:978px">Strideon</div>
  <div class="abs arrow" style="left:1170px">›</div>
</section>

<!-- AWARDS -->
<section>
  <div class="abs" style="left:0;top:4469px;width:1200px;height:263px;background:var(--band)"></div>
  <h2 class="abs sec-title" style="top:4506px"><b>AWARDS</b></h2>
  <div class="abs gold-line" style="left:566px;top:4568px"></div>
  <div class="abs" style="left:260px;top:4618px;width:94px;height:72px;border-radius:50%;background:#e9c64a"></div>
  <div class="abs" style="left:426px;top:4620px;width:130px;height:66px;border-radius:50%;background:#d8c27a"></div>
  <div class="abs" style="left:630px;top:4616px;width:94px;height:74px;border-radius:8px;background:#3f4a52"></div>
  <div class="abs" style="left:806px;top:4618px;width:76px;height:72px;background:#ece3c6"></div>
</section>

<!-- FOOTER -->
<footer>
  <div class="abs brand-mark" style="left:130px;top:4838px"><span class="brand-dot"></span>Floravine pte ltd</div>
  <div class="abs" style="left:250px;top:4878px;width:48px;height:26px;background:#f3dcd4"></div>

  <div class="abs" style="left:368px;top:4790px">
    <div class="foot-head">CONTACT US</div>
    <div class="foot-list">21 Fernleaf Road<br>#04-11<br>Verdant House<br>Singapore 150421<br>Tel: +65 6100 2233<br>Mobile: +65 9100 4455<br>Email: hello@floravine.example</div>
  </div>
  <div class="abs" style="left:630px;top:4790px">
    <div class="foot-head">MENU</div>
    <div class="foot-list" style="line-height:17.6px">Home<br>Services<br>Gallery<br>Calculator<br>Portfolio<br>Testimonials<br>Contact<br>Blog</div>
  </div>

  <div class="abs" style="left:802px;top:4788px;width:188px;height:64px;background:var(--white);box-shadow:0 1px 6px rgba(0,0,0,.15);border-radius:4px;padding:12px 14px;font-size:11.5px;line-height:15px;color:var(--ink-soft)">Hello! Do you have any questions? I'm happy to help
    <span style="position:absolute;right:8px;top:4px;font-size:14px;color:var(--ink)">×</span></div>
  <div class="abs" style="left:1011px;top:4791px;width:52px;height:52px;border-radius:50%;background:var(--accent)">
    <svg width="52" height="52" viewBox="0 0 52 52" fill="none" stroke="#fff" stroke-width="2.2"><path d="M15 18h22v14H24l-6 5v-5h-3z"/><path d="M20 24h12M20 28h8"/></svg>
  </div>
  <div class="abs" style="left:880px;top:4890px;width:124px;height:78px;border-radius:6px;background:#efeaea"></div>

  <div class="abs" style="left:133px;top:5019px;width:934px;height:1px;background:var(--rule)"></div>
  <p class="abs" style="left:0;width:1200px;top:5046px;text-align:center;font-size:11px;color:var(--ink-soft)">© Copyright 2023 | Floravine Pte Ltd. (Singapore) - Office Design and Renovation. All Rights Reserved. Privacy Policy | Terms and Conditions</p>
</footer>

</body>
</html>
```